Bed & Breakfast Wordpress Theme - Design Only

We are looking for a Wordpress theme for an award winning UK Bed & Breakfast (Guesthouse) www.brambleinn.co.uk
You will see that the current site is basic and dated, we need a new site that showcases the very high standard of rooms on offer and is geared towards both mobile and desktop browsing.
We would like the colours that have been used in the rooms and building (as seen on the current website) to feature in the design.
We particularly like the look of this accommodation provider website: http://www.wrenmeadowbarns.co.uk
Selected website images can be downloaded here, feel free to use more from the existing website too:
https://www.filecrate.example/s/qx83kd01zzp4mnt/website%20images.zip
Target Market(s)
The accommodation is upmarket and the design needs to subtly communicate this.
The accommodation attracts a varied mix of ages so needs to be up scale without being overly modern.
Industry/Entity Type
Accommodation
Requirements
Must have
- As the accommodation does not have a logo we need a basic typographic logo incorporated into the design.
Colours of the building and rooms must be integrated into the design in some way.
A bold homepage that allows images of the rooms on offer and key information to be visibale above the fold. The goal of the homepage is for someone to then click Rooms or Prices so calls to action may help here.
Separate designs for a sidebar and full width version of sub pages.
An area that shows off the awards won by the company on all pages and space for testimonials.
The site must enable an easy transition from - homepage - to rooms - to prices with possible call to action buttons in the top right corner on these pages
The site needs to have a Homepage layout, a general sub page layout, and a 'Rooms' page layout which will showcase all rooms available possibly in a grid layout.
Nice to have
- Please use some of the images available currently on the website in your mockup, particularly of the building and rooms.
Should not have
- No need for any type of booking fields or engine as the booking system will be embedded on a full width page.

```html
<!DOCTYPE html>
<html lang="en">
<head>
<meta charset="utf-8">
<title>Bramble Inn – A small and friendly hotel</title>
<link rel="stylesheet" href="https://fonts.googleapis.com/css2?family=Open+Sans:ital,wght@0,400;0,600;1,400&family=Ubuntu:wght@400;500&display=swap">
<style>
:root{
  --gold:#c2a865;
  --gold-light:#d8c48c;
  --gold-text:#b8974a;
  --dark:#3b3b3b;
  --darker:#2e2e2e;
  --page:#efefef;
  --panel:#ffffff;
  --ink:#333333;
  --muted:#777777;
  --link-green:#5a7a2a;
}
*{margin:0;padding:0;box-sizing:border-box}
html,body{width:800px;height:1200px;overflow:hidden}
body{position:relative;background:var(--page);font-family:"Open Sans",sans-serif;color:var(--ink)}
.abs{position:absolute}
.site-header{left:0;top:0;width:800px;height:109px;background:linear-gradient(#474747,#333)}
.logo{left:88px;top:32px;font-family:"Ubuntu",sans-serif;font-weight:500;font-size:27px;letter-spacing:2px;color:#fff;text-transform:uppercase}
.tagline{left:158px;top:63px;font-size:13px;color:var(--gold-light)}
.address{right:86px;top:15px;font-size:10.5px;font-style:italic;color:#ccc}
.phone{right:86px;top:40px;font-size:17px;color:#fff;display:flex;align-items:center;gap:10px}
.email{right:86px;top:67px;font-size:10.5px;color:#fff;display:flex;align-items:center;gap:10px}
.content-panel{left:80px;top:109px;width:640px;height:835px;background:var(--panel)}
.main-nav{left:87px;top:92px;width:626px;height:29px;background:linear-gradient(#d5bf83,var(--gold));display:flex;align-items:center}
.main-nav a{color:#fff;font-size:8.6px;font-weight:600;text-decoration:none;text-transform:uppercase;margin-left:11px;margin-right:15px}
.slider{left:87px;top:122px;width:626px;height:276px;border:1px solid #ccc;background:linear-gradient(100deg,#6a4a2a 0%,#b5895a 30%,#d7b27c 50%,#8a6840 75%,#5a3e24 100%)}
.slide-caption{left:88px;top:222px;width:436px;height:76px;background:rgba(30,30,30,.72);padding:4px 0 0 30px;font-family:"Ubuntu",sans-serif}
.slide-caption .l1{font-size:27px;color:#fff}
.slide-caption .l2{font-size:30px;color:var(--gold-light);margin-top:-4px}
.dots{left:372px;top:375px;display:flex;gap:5px}
.dots span{width:11px;height:11px;border-radius:50%;background:var(--gold)}
.dots span:first-child{background:#222}
.welcome-img{left:94px;top:425px;width:206px;height:137px;background:linear-gradient(90deg,#e2ddd4,#cfc8bd 60%,#9a8d7a)}
.welcome-title{left:314px;top:420px;font-family:"Ubuntu",sans-serif;font-size:17px;color:var(--ink)}
.welcome-text{left:314px;top:445px;width:392px;font-size:8.6px;line-height:15.3px;color:#666}
.learn-more{left:314px;top:541px;font-size:10px;color:var(--gold-text);letter-spacing:.5px}
.divider{left:87px;top:577px;width:626px;border-top:1px dotted var(--gold)}
.video-title{left:87px;top:589px;width:250px;font-family:"Ubuntu",sans-serif;font-size:14px;line-height:16.5px}
.video{left:87px;top:644px;width:252px;height:159px;border:1px solid #ccc;background:linear-gradient(160deg,#7a9bb0 0%,#eee 35%,#dcdcd2 55%,#4f6a3a 80%,#3b4f2c)}
.reviews{left:354px;top:591px;width:146px;height:213px;border:1px solid #ddd;background:#fafafa}
.reviews .brand{position:absolute;left:10px;top:7px;font-family:"Ubuntu",sans-serif;font-size:15px;color:#333;display:flex;align-items:center;gap:5px}
.reviews .brand i{width:10px;height:10px;border-radius:50%;background:#6a9a3a;display:block}
.reviews h4{position:absolute;left:10px;top:32px;width:130px;font-weight:400;font-size:10.2px;line-height:14px}
.reviews ul{position:absolute;left:10px;top:65px;width:130px;list-style:none;font-size:7.6px;color:var(--link-green);font-weight:600}
.reviews li{margin-bottom:7px;line-height:11px}
.reviews .links{position:absolute;left:10px;top:172px;font-size:7.6px;color:#333}
.reviews .copy{position:absolute;left:0;top:193px;width:100%;border-top:1px solid #ddd;padding:3px 10px;font-size:7.6px;color:#999}
.sidebar{left:513px;top:591px;width:200px;height:341px;background:var(--dark)}
.social{left:558px;top:611px;display:flex;gap:9px}
.social span{width:21px;height:21px;border-radius:50%;background:#7aa6d6;border:2px solid #dfe9f5}
.sidebar-rule{left:523px;top:646px;width:181px;border-top:1px dotted #666}
.gallery{left:522px;top:655px;width:183px;height:184px;background:var(--gold)}
.gallery .title{position:absolute;left:7px;top:4px;font-family:"Ubuntu",sans-serif;font-size:14px;color:#fff}
.gallery .arrows{position:absolute;right:7px;top:4px;color:#fff;font-size:13px;letter-spacing:6px}
.gallery .photo{position:absolute;left:8px;top:30px;width:167px;height:148px;border:2px solid #ddd;background:linear-gradient(90deg,#c9b89a,#7a5a3a 40%,#e9ddc5 70%,#a88f6a)}
.vouchers{left:523px;top:870px;width:182px;height:37px;background:linear-gradient(#d9c58d,var(--gold));display:flex;align-items:center;padding-left:23px;gap:12px;font-family:"Ubuntu",sans-serif;font-size:14px;color:var(--darker)}
.tile{top:816px;width:201px;height:116px;display:flex}
.tile .label{width:93px;background:var(--gold);color:#fff;font-size:12px;letter-spacing:.5px;display:flex;align-items:center;justify-content:center}
.tile .photo{width:108px}
.tile.rooms{left:87px}
.tile.rooms .photo{background:linear-gradient(90deg,#e8e1d4,#a8865c 45%,#f0ece4)}
.tile.tariffs{left:299px}
.tile.tariffs .photo{background:linear-gradient(90deg,#d9d6d0,#2e2e2e 40%,#8a5c4a 75%,#d0c9bc)}
.site-footer{left:0;top:944px;width:800px;height:256px;background:var(--dark)}
.f-head{top:958px;font-family:"Ubuntu",sans-serif;font-size:14px;color:var(--gold-light)}
.quote{left:87px;top:986px;width:200px;font-size:8.6px;font-style:italic;line-height:15.3px;color:#fff}
.quote-mark{font-family:"Ubuntu",sans-serif;font-size:26px;color:#777;font-style:normal;float:left;line-height:18px;margin-right:6px}
.quote-by{left:87px;top:1111px;font-size:8.6px;color:var(--gold-light)}
.quote-date{left:87px;top:1126px;font-size:8.6px;color:#fff}
.badge{background:#fff;border:1px solid #ccc}
.map{left:500px;top:985px;width:213px;height:130px;background:linear-gradient(135deg,#eef0e4,#dfe8d0 55%,#cbdcea 85%,#b9d1e8)}
.legal{left:87px;top:1164px;font-size:8px;line-height:13.5px;color:#ccc}
.foot-nav{right:87px;top:1172px;font-size:8px;color:#aaa}
</style>
</head>
<body>
<header class="site-header abs"></header>
<div class="logo abs">Bramble Inn</div>
<div class="tagline abs">A small and friendly hotel.</div>
<div class="address abs">Bramble Inn, Hollin Lane, Ashcombe, Hampshire SO41 9QX</div>
<div class="phone abs">
  <svg width="19" height="13" viewBox="0 0 19 13"><path d="M1 5 Q9.5-1 18 5 L16 7 L13 5 V3 H6 V5 L3 7Z" fill="#c2a865"/><rect x="4" y="6" width="11" height="7" rx="1" fill="#c2a865"/></svg>
  01632 960418</div>
<div class="email abs">
  <svg width="18" height="12" viewBox="0 0 18 12"><rect x=".5" y=".5" width="17" height="11" fill="none" stroke="#c2a865"/><path d="M.5 .5 L9 7 L17.5 .5" fill="none" stroke="#c2a865"/></svg>
  enquiries@brambleinn.co.uk</div>

<div class="content-panel abs"></div>
<nav class="main-nav abs">
  <a>Home</a><a>Rooms</a><a>Prices</a><a>Picture Gallery</a><a style="margin-left:20px">Book Online</a><a style="margin-left:18px">Information</a><a style="margin-left:12px">Offers</a><a style="margin-left:18px">Contact Us</a>
</nav>

<div class="slider abs" role="img" aria-label="Bedroom with wooden four-poster bed and warm wall lights"></div>
<div class="slide-caption abs"><div class="l1">Bramble Inn is a:</div><div class="l2">‘Small and Friendly Hotel'</div></div>
<div class="dots abs"><span></span><span></span><span></span><span></span></div>

<div class="welcome-img abs" role="img" aria-label="Hallway wall with a welcome message lettered on it"></div>
<h2 class="welcome-title abs" style="font-weight:400">Welcome to Bramble Inn</h2>
<p class="welcome-text abs">Aliquam molestie, mi et imperdiet euismod, dui purus auctor tellus, et interdum lacus lectus et ante. Sed accumsan sollicitudin sapien, sit amet adipiscing turpis gravida ac. In congue, neque ac lobortis volutpat, libero mauris varius mi, vitae suscipit ipsum ligula vitae risus. Duis aliquam nibh a dui iaculis viverra id a velit. Vivamus egestas risus in magna varius commodo. Sed semper viverra egestas. Etiam pretium porttitor lectus, vel ornare neque porta volutpat.</p>
<div class="learn-more abs">LEARN MORE</div>
<div class="divider abs"></div>

<div class="video-title abs">Bramble Inn New Forest Small and friendly hotel. Formerly a 5 star B&amp;B VIDEO BELOW</div>
<div class="video abs" role="img" aria-label="Video still of the white cottage front with a yellow door"></div>

<aside class="reviews abs">
  <div class="brand"><i></i>TravelNotes</div>
  <h4>Most Recent Traveller Reviews:</h4>
  <ul>
    <li>17 Dec 2013: “Lovely Stay”</li>
    <li>9 Dec 2013: “Charming and very relaxing!”</li>
    <li>2 Dec 2013: “Perfection”</li>
    <li>2 Dec 2013: “Wonderful B&amp;B”</li>
    <li>18 Nov 2013: “Excellent”</li>
  </ul>
  <div class="links">Read reviews &nbsp;|&nbsp; Write a review</div>
  <div class="copy">© 2013 TravelNotes Ltd</div>
</aside>

<aside class="sidebar abs"></aside>
<div class="social abs"><span></span><span></span><span></span><span></span></div>
<div class="sidebar-rule abs"></div>
<div class="gallery abs">
  <div class="title">Gallery</div><div class="arrows">‹ ›</div>
  <div class="photo" role="img" aria-label="Bedroom with a driftwood bed and chandelier"></div>
</div>
<div class="vouchers abs">
  <svg width="24" height="24" viewBox="0 0 24 24"><rect x="1" y="8" width="22" height="5" fill="#2e2e2e"/><rect x="3" y="13" width="18" height="10" fill="#2e2e2e"/><rect x="11" y="8" width="2" height="15" fill="#c2a865"/><path d="M12 8 C8 1 3 4 6 8 M12 8 C16 1 21 4 18 8" fill="none" stroke="#2e2e2e" stroke-width="2"/></svg>
  Gift Vouchers</div>

<div class="tile rooms abs"><div class="label">ROOMS</div><div class="photo" role="img" aria-label="Bright bedroom with a rustic timber bed"></div></div>
<div class="tile tariffs abs"><div class="photo" role="img" aria-label="Wood-burning stove beside an armchair"></div><div class="label">TARIFFS</div></div>

<footer class="site-footer abs"></footer>
<h3 class="f-head abs" style="left:87px;font-weight:400">What Our Customer Says..</h3>
<p class="quote abs"><span class="quote-mark">“</span>This really is the perfect hideaway! The cottage is wonderful &amp; your attention to detail fantastic! I wish I could recommend things to do but the cottage was so comfortable that we didn't venture out! We'll definitely be back at summer to sit outside &amp; enjoy the sun in the courtyard... Thank you!</p>
<div class="quote-by abs">Helen &amp; Mark, Leeds</div>
<div class="quote-date abs">December 2013</div>

<h3 class="f-head abs" style="left:319px;font-weight:400">Awards</h3>
<div class="badge abs" style="left:319px;top:987px;width:44px;height:67px" role="img" aria-label="Tourism excellence award badge"></div>
<div class="abs" style="left:368px;top:997px;width:57px;height:57px;background:#fff;display:flex;align-items:center;justify-content:center" role="img" aria-label="Regional food award badge"><span style="width:44px;height:44px;border-radius:50%;background:#2d3f78;display:block"></span></div>
<div class="badge abs" style="left:319px;top:1058px;width:134px;height:57px" role="img" aria-label="Regional tourism awards 2008 winner certificate"></div>

<h3 class="f-head abs" style="left:500px;font-weight:400">Find Us</h3>
<div class="map abs" role="img" aria-label="Map of the surrounding villages and coastline"></div>

<div class="legal abs">© 2013 Bramble Inn | Privacy Policy<br>Terms &amp; Conditions</div>
<div class="foot-nav abs">Home | Rooms | Tariffs | Activities | Eating &amp; Drinking | Travel | Links | Sitemap</div>
</body>
</html>
```